Brookvane Consulting Business Card Design

Business Card Design for Brookvane Consulting. Brookvane Consulting is a boutique consultancy based in Atlanta, GA., that specializes in marketing strategy, organization planning, and leadership development. We provide solutions for small businesses and startups as well as Vantage 300 companies.

http://brookvaneconsulting.com/

Target Market(s)

We provide solutions for small businesses and startups as well as Vantage 300 companies.

Industry/Entity Type

Consulting

Contact Information for Business Card

Two sided business card with priority on contact information, logo, tag line (Inspiration to Dream More, Do More, Become More)

Colors

Designer to choose colors to be used in the design.

Requirements
Must have
• contact information, logo, tag line (Inspiration to Dream More, Do More, Become More)
• Simple no over communication.
Nice to have
• I would like to see different placements of logo and creative use of both sides of the card
Should not have
• Do not put too much information on the card.

```html
<!DOCTYPE html>
<html lang="en">
<head>
<meta charset="utf-8">
<title>Brookvane Consulting Business Card</title>
<link rel="stylesheet" href="https://fonts.googleapis.com/css2?family=Roboto:wght@400;500&family=Roboto+Condensed:wght@500&display=swap">
<style>
  :root {
    --backdrop: #e9e6e1;
    --card: #232425;
    --card-edge: #1a1b1c;
    --ink-light: #ffffff;
    --ink-muted: #c9c9c9;
    --ink-name: #b5b5b5;
    --rule: #5a5b5c;
    --band: #f4f4f4;
    --band-ink: #222222;
  }
  * { margin: 0; padding: 0; box-sizing: border-box; }
  html, body { width: 1200px; height: 960px; overflow: hidden; }
  body {
    background: var(--backdrop);
    font-family: "Roboto", Arial, sans-serif;
    position: relative;
  }
  .card {
    position: absolute;
    width: 600px;
    height: 342px;
    background: var(--card);
    box-shadow: 0 3px 8px rgba(0,0,0,0.35);
    overflow: hidden;
  }
  .card-front { left: 330px; top: 100px; }
  .card-back { left: 320px; top: 493px; }

  .front-pattern {
    position: absolute; inset: 0;
    background: linear-gradient(180deg, #262728 0%, #202122 100%);
  }
  .front-logo {
    position: absolute; left: 0; right: 0; top: 135px;
    text-align: center;
    color: var(--ink-light);
    font-weight: 500;
    font-size: 38px;
    letter-spacing: 1px;
  }
  .front-tagline {
    position: absolute; left: 0; right: 0; top: 289px;
    text-align: center;
    color: var(--ink-muted);
    font-size: 14px;
  }

  .back-logo {
    position: absolute; left: 58px; top: 132px;
    color: var(--ink-light);
    font-weight: 500;
    font-size: 30px;
    line-height: 36px;
    letter-spacing: 0.5px;
  }
  .back-divider {
    position: absolute; left: 302px; top: 125px;
    width: 1px; height: 94px;
    background: var(--rule);
  }
  .contact { position: absolute; left: 329px; top: 124px; }
  .contact-name {
    font-family: "Roboto Condensed", Arial, sans-serif;
    font-weight: 500;
    font-size: 21px;
    color: var(--ink-name);
    letter-spacing: 0.3px;
  }
  .contact-title {
    font-weight: 500;
    font-size: 15px;
    color: var(--ink-light);
    margin-top: 4px;
  }
  .contact-line {
    font-size: 14px;
    color: var(--ink-muted);
    line-height: 19px;
  }
  .contact-phone { margin-top: 12px; }

  .web-band { position: absolute; left: 0; bottom: 0; width: 600px; height: 30px; }
  .web-address {
    position: absolute; left: 14px; bottom: 7px;
    font-size: 13px; font-weight: 500;
    letter-spacing: 1px;
    color: var(--band-ink);
  }
</style>
</head>
<body>
  <section class="card card-front" aria-label="Card front">
    <div class="front-pattern" role="img" aria-label="Subtle dark grid texture"></div>
    <div class="front-logo">Brookvane Consulting</div>
    <p class="front-tagline">Inspiration to Dream More, Do More, Become More</p>
  </section>

  <section class="card card-back" aria-label="Card back">
    <div class="back-logo">Brookvane<br>Consulting</div>
    <div class="back-divider"></div>
    <div class="contact">
      <div class="contact-name">DARIUS WHITFIELD</div>
      <div class="contact-title">Founder/Managing Director</div>
      <div class="contact-line contact-phone">P. 404-555-0182</div>
      <div class="contact-line">darius@brookvaneconsulting.com</div>
    </div>
    <svg class="web-band" viewBox="0 0 600 30" aria-hidden="true">
      <polygon points="0,2 242,2 262,22 600,22 600,30 0,30" fill="var(--band)"/>
      <polygon points="250,2 600,2 600,14 262,14" fill="var(--band)"/>
      <polygon points="246,0 252,0 268,16 262,16" fill="var(--card)"/>
    </svg>
    <div class="web-address">www.brookvaneconsulting.com</div>
  </section>
</body>
</html>
```